Oil Field Service company needs professional business cards

Looking to clean up our current company business cards and look a little more professional. Brenwick Casing Services is a US based company that services the oil field. We deal with engineers, managers and oil rigs....................................................................................................................................................................................................................................................................................................................................................................................................

Target Market(s)

Oil and Gas professionals

Industry/Entity Type

Oil And Gas

Contact Information for Business Card

See attached photo as example

Font styles to use
Sans Serif

Colors
ec1f27

Requirements
Must have
• Company Logo, Name, Title, Cell, Office, Fax, Email.
• See attached photo
Nice to have
• External CRT, Internal CRT, Casing Crews, Torque Turn, Laydown Machine
Should not have
• Do not introduce any new pictures and keep it professional looking

```html
<!DOCTYPE html>
<html lang="en">
<head>
<meta charset="utf-8">
<title>Brenwick Casing Services – Business Card</title>
<link rel="stylesheet" href="https://fonts.googleapis.com/css2?family=Source+Sans+3:wght@400;600;700&display=swap">
<style>
  :root {
    --brand-red: #ec1f27;
    --ink: #3b4650;
    --ink-soft: #4a525a;
    --icon-grey: #a3a8ad;
    --card-white: #ffffff;
    --backdrop: #e7e7e7;
  }
  * { margin: 0; padding: 0; box-sizing: border-box; }
  html, body {
    width: 1200px; height: 1200px; overflow: hidden;
    background: var(--backdrop);
    font-family: "Source Sans 3", sans-serif;
  }
  .card {
    position: absolute;
    left: 80px; top: 307px;
    width: 1040px; height: 585px;
    background: var(--card-white);
  }
  .brand {
    position: absolute;
    left: 0; right: 0; top: 108px;
    display: flex; justify-content: center; align-items: center; gap: 14px;
  }
  .brand-mark {
    width: 22px; height: 22px; background: var(--brand-red);
  }
  .brand-name {
    font-size: 40px; font-weight: 700; color: var(--ink);
    letter-spacing: 0.5px;
  }
  .person {
    position: absolute; left: 122px; top: 348px;
  }
  .person-name {
    font-size: 36px; font-weight: 700; color: var(--brand-red); line-height: 1;
  }
  .person-title {
    margin-top: 10px;
    font-size: 21px; font-weight: 400; color: var(--ink-soft); line-height: 1;
  }
  .contact {
    position: absolute; left: 0; top: 0; width: 100%; height: 100%;
  }
  .contact-row {
    position: absolute; left: 580px;
    display: flex; align-items: center; height: 30px;
    font-size: 22px; color: var(--ink-soft);
  }
  .contact-row svg {
    width: 22px; height: 22px; margin-right: 15px; fill: var(--icon-grey);
  }
  .contact-row.phone { font-weight: 600; color: var(--ink); }
  .row-address { top: 285px; }
  .row-cell { top: 337px; }
  .row-office { top: 369px; }
  .row-fax { top: 402px; }
  .row-email { top: 454px; }
  .service-band {
    position: absolute; left: 0; bottom: 0; width: 100%; height: 66px;
  }
  .band-block {
    position: absolute; top: 0; height: 66px; width: 150px; background: var(--brand-red);
  }
  .band-block.left { left: 0; }
  .band-block.right { right: 0; }
  .service-list {
    position: absolute; left: 150px; right: 150px; top: 0; height: 66px;
    display: flex; justify-content: center; align-items: center; gap: 12px;
    font-size: 20px; font-weight: 600; letter-spacing: 0.6px; color: var(--ink-soft);
    white-space: nowrap;
  }
  .service-list .accent { color: var(--brand-red); }
</style>
</head>
<body>
  <div class="card">
    <div class="brand">
      <span class="brand-mark"></span>
      <span class="brand-name">Brenwick Casing Services</span>
    </div>

    <div class="person">
      <div class="person-name">Wade Holloway</div>
      <div class="person-title">AREA MANAGER</div>
    </div>

    <div class="contact">
      <div class="contact-row row-address">
        <svg viewBox="0 0 24 24" aria-hidden="true"><path d="M12 2a7 7 0 0 0-7 7c0 5 7 13 7 13s7-8 7-13a7 7 0 0 0-7-7zm0 9.5A2.5 2.5 0 1 1 12 6.5a2.5 2.5 0 0 1 0 5z"/></svg>
        harlow, OK 73840
      </div>
      <div class="contact-row phone row-cell">
        <svg viewBox="0 0 24 24" aria-hidden="true"><path d="M7 2h10a1.5 1.5 0 0 1 1.5 1.5v17A1.5 1.5 0 0 1 17 22H7a1.5 1.5 0 0 1-1.5-1.5v-17A1.5 1.5 0 0 1 7 2zm1 3v9h8V5H8zm2 12v2h4v-2h-4z"/></svg>
        555 218 4630
      </div>
      <div class="contact-row phone row-office">
        <svg viewBox="0 0 24 24" aria-hidden="true"><path d="M6.6 10.8a15.1 15.1 0 0 0 6.6 6.6l2.2-2.2a1 1 0 0 1 1-.25 11.4 11.4 0 0 0 3.6.57 1 1 0 0 1 1 1V20a1 1 0 0 1-1 1A17 17 0 0 1 3 4a1 1 0 0 1 1-1h3.5a1 1 0 0 1 1 1c0 1.25.2 2.45.57 3.6a1 1 0 0 1-.25 1z"/></svg>
        555 407 1952
      </div>
      <div class="contact-row phone row-fax">
        <svg viewBox="0 0 24 24" aria-hidden="true"><path d="M7 3h10v5H7zM4 9h16a2 2 0 0 1 2 2v6h-4v4H6v-4H2v-6a2 2 0 0 1 2-2zm4 6v4h8v-4H8z"/></svg>
        555 218 4671
      </div>
      <div class="contact-row row-email">
        <svg viewBox="0 0 24 24" aria-hidden="true"><path d="M2 5h20v14H2zm2 2v.5l8 5.5 8-5.5V7l-8 5.5z"/></svg>
        wadeholloway@brenwickservice.com
      </div>
    </div>

    <div class="service-band">
      <div class="band-block left"></div>
      <div class="service-list">
        <span>External CRT</span>
        <span class="accent">Internal CRT</span>
        <span>Casing Crews</span>
        <span class="accent">Torque Turn</span>
        <span>Laydown Machine</span>
      </div>
      <div class="band-block right"></div>
    </div>
  </div>
</body>
</html>
```